Corvane Capital Business Cards

These are professional business cards that are for my family office.
Put fake emails and phone numbers as of now until I finalize those components. This family office controls my families investments, assets, and future. The cards should be professional.
..
.
.
.
I just uploaded another variation of a logo I would like to see as a business card to I am inbeteen which logo to use

Target Market(s)

business

Industry/Entity Type

business

Contact Information for Business Card

Professional, wealth related, finance related.

Requirements
Must have
• Logo

```html
<!DOCTYPE html>
<html lang="en">
<head>
<meta charset="UTF-8">
<title>Corvane Capital Business Cards</title>
<link rel="stylesheet" href="https://fonts.googleapis.com/css2?family=Playfair+Display:wght@400;500&family=Poppins:wght@300;400&display=swap">
<style>
  :root {
    --canvas-grey: #c4c4c4;
    --card-black: #000000;
    --card-white: #ffffff;
    --gold: #c4a96a;
    --ink-light: #ffffff;
  }
  * { box-sizing: border-box; margin: 0; padding: 0; }
  html, body {
    width: 1200px;
    height: 1015px;
    overflow: hidden;
    background: var(--canvas-grey);
  }
  .canvas {
    position: relative;
    width: 1200px;
    height: 1015px;
  }
  .card {
    position: absolute;
    width: 560px;
    height: 320px;
    box-shadow: 0 10px 24px rgba(0,0,0,0.35);
  }
  .card--front {
    left: 70px;
    top: 110px;
    background: var(--card-black);
    display: flex;
    align-items: center;
    justify-content: center;
  }
  .brand-name {
    font-family: "Playfair Display", serif;
    font-weight: 400;
    font-size: 44px;
    letter-spacing: 4px;
    text-transform: uppercase;
    color: var(--ink-light);
  }
  .card--back {
    left: 570px;
    top: 585px;
    background: var(--card-white);
    display: flex;
    align-items: center;
    justify-content: center;
  }
  .contact-ring {
    width: 296px;
    height: 296px;
    border-radius: 50%;
    border: 1.5px solid var(--gold);
    display: flex;
    align-items: center;
    justify-content: center;
  }
  .contact-disc {
    width: 270px;
    height: 270px;
    border-radius: 50%;
    background: var(--card-black);
    display: flex;
    flex-direction: column;
    align-items: center;
    justify-content: center;
    text-align: center;
    color: var(--ink-light);
    font-family: "Poppins", sans-serif;
    font-weight: 300;
  }
  .person-name {
    font-family: "Playfair Display", serif;
    font-weight: 500;
    font-size: 17px;
    letter-spacing: 1.5px;
    text-transform: uppercase;
    color: var(--gold);
  }
  .person-title {
    font-size: 12px;
    margin-top: 1px;
  }
  .divider {
    width: 34px;
    height: 1px;
    background: var(--gold);
    margin: 9px 0;
  }
  .contact-line {
    font-size: 11.5px;
    line-height: 1.35;
  }
</style>
</head>
<body>
  <main class="canvas">
    <section class="card card--front" aria-label="Card front">
      <h1 class="brand-name">Corvane Capital</h1>
    </section>

    <section class="card card--back" aria-label="Card back">
      <div class="contact-ring">
        <div class="contact-disc">
          <p class="person-name">Elliot Marsh</p>
          <p class="person-title">Managing Director</p>
          <span class="divider"></span>
          <p class="contact-line">020-555 014 732</p>
          <p class="contact-line">hello@corvanemail.com</p>
          <p class="contact-line">www.corvanecapital.example</p>
          <span class="divider"></span>
          <p class="contact-line">421, Address line goes here</p>
          <p class="contact-line">45452,Country Name</p>
        </div>
      </div>
    </section>
  </main>
</body>
</html>
```